Design and Renovation Company Luxury Business Card

I want to create a luxury business card for a Design and Renovation Firm . We will use our current logo. The company name is 528BUILDA. We do not want anything standard. We need a very unique concept.
Please see uploaded inspiration. I really like the textured paper option. I would like the card to be thick with debossing, and/or embossing options. The logo has orange in it but I would like to see the card with and without the orange. I think the orange may make the company feel less high-end. The goal is to elevate the logo not match its vibe per se of the logo. We want something very unique, not standard at all!
I would like a space for :
Logo,
Name,
Position,
Email,
Office number,
Website Address,
Business Address,
Thank you!
Have fun!
Target Market(s)
Home owners Age 35 +
Industry/Entity Type
Design and Renovation
Contact Information for Business Card
Logo, Name, Position, Email, Office number, Website Address, Business Address,.
Colors
Designer to choose colors to be used in the design.
Requirements
Must have
- A luxury designer feel. Must be black or dark grey but open to other luxury ideas.
Nice to have
- Gold, silver, black embossing or debossing. Textured paper design.
Should not have
- A cheap look and feel.

```html
<!DOCTYPE html>
<html lang="en">
<head>
<meta charset="utf-8">
<title>528BUILDA Business Card</title>
<link href="https://fonts.googleapis.com/css2?family=Montserrat:wght@400;500;700&family=Questrial&display=swap" rel="stylesheet">
<style>
  :root{
    --stage:#8a7559;
    --card-white:#ffffff;
    --ink:#1c1c1c;
    --ink-deep:#0c0c0c;
    --orange:#f7931e;
    --text-light:#f2f2f2;
    --text-muted:#d9d9d9;
  }
  *{margin:0;padding:0;box-sizing:border-box}
  html,body{width:900px;height:1200px;overflow:hidden}
  body{background:var(--stage);position:relative;font-family:"Montserrat",sans-serif}
  .card{position:absolute;left:80px;width:742px;height:440px;border-radius:22px;overflow:hidden;box-shadow:0 6px 14px rgba(0,0,0,.35)}
  .card-front{top:131px;background:var(--card-white)}
  .card-back{top:639px;background:var(--ink)}
  .front-waves{position:absolute;inset:0;width:742px;height:440px}
  .brand-front{position:absolute;left:482px;top:204px;display:flex;align-items:center;gap:10px}
  .brand-mark{width:22px;height:22px;background:var(--orange)}
  .brand-front .brand-name{font-family:"Questrial",sans-serif;font-size:33px;color:var(--ink-deep);letter-spacing:1px}
  .person{position:absolute;left:32px;top:250px}
  .person-name{font-size:26px;font-weight:700;color:var(--orange)}
  .person-role{font-size:16px;color:var(--text-muted);margin-top:4px}
  .contacts{position:absolute;left:32px;top:333px;list-style:none}
  .contacts li{display:flex;align-items:center;gap:8px;height:28.5px;font-size:16px;color:var(--text-light)}
  .contacts svg{width:16px;height:16px;fill:var(--orange)}
  .address{position:absolute;left:485px;top:373px;font-size:16px;line-height:21px;color:var(--text-light)}
  .back-texture{position:absolute;inset:0;background:linear-gradient(90deg,#050505 0%,#1a1a1a 45%,#3a3a3a 80%,#555 100%)}
  .brand-back{position:absolute;left:284px;top:274px}
  .brand-back-row{display:flex;align-items:center;gap:12px}
  .brand-back .brand-mark{width:32px;height:32px}
  .brand-back .brand-name{font-family:"Questrial",sans-serif;font-size:54px;line-height:56px;color:var(--card-white);letter-spacing:2px}
  .tagline{font-size:13.5px;font-weight:500;color:var(--card-white);letter-spacing:2.6px;margin:2px 0 0 80px}
</style>
</head>
<body>
  <section class="card card-front">
    <svg class="front-waves" viewBox="0 0 742 440" aria-hidden="true">
      <path d="M0,200 C130,150 270,160 400,225 C520,285 620,330 742,290 L742,440 L0,440 Z" fill="var(--ink)"/>
      <path d="M0,172 C140,120 290,145 440,222 C560,285 660,285 742,190 L742,240 C650,335 540,330 420,262 C290,190 150,160 0,182 Z" fill="var(--orange)"/>
      <path d="M0,252 C120,200 250,195 380,250 C500,300 600,345 742,325" fill="none" stroke="var(--card-white)" stroke-width="3"/>
    </svg>
    <div class="brand-front"><span class="brand-mark"></span><span class="brand-name">528BUILDA</span></div>
    <div class="person">
      <p class="person-name">Daniel Harper</p>
      <p class="person-role">Managing Director</p>
    </div>
    <ul class="contacts">
      <li><svg viewBox="0 0 24 24"><path d="M6.6 10.8a15 15 0 0 0 6.6 6.6l2.2-2.2c.3-.3.7-.4 1-.2 1.1.4 2.3.6 3.6.6.6 0 1 .4 1 1V20c0 .6-.4 1-1 1A17 17 0 0 1 3 4c0-.6.4-1 1-1h3.5c.6 0 1 .4 1 1 0 1.3.2 2.5.6 3.6.1.3 0 .7-.2 1z"/></svg>555-014-2288</li>
      <li><svg viewBox="0 0 24 24"><path d="M2 5h20v2l-10 6L2 7zm0 4l10 6 10-6v10H2z"/></svg>info@528builda.com</li>
      <li><svg viewBox="0 0 24 24"><circle cx="12" cy="12" r="10"/></svg>www.528builda.com</li>
    </ul>
    <p class="address">415 Maple Grove Ave, #112<br>Lakeview, OH 43210</p>
  </section>

  <section class="card card-back">
    <div class="back-texture" role="img" aria-label="Embossed grid of dark squares fading from black to grey"></div>
    <div class="brand-back">
      <div class="brand-back-row"><span class="brand-mark"></span><span class="brand-name">528BUILDA</span></div>
      <p class="tagline">Design and Renovation Firm</p>
    </div>
  </section>
</body>
</html>
```